Coffee Bag Design for Tollbury Coffee

We’re excited to invite you to help us bring Tollbury Coffee to life on grocery store shelves with a design that embodies our mission of spreading goodness and creating a lasting impact. Tollbury Coffee represents warmth, positivity, and the power of small actions to create ripples of goodness. Each cup not only offers a rich, gourmet coffee experience but also gives back to the community, with $2 from each bag supporting local food banks.

To reflect this vision, we’d love for the design to feature a dark (greyish) blue as the base color to convey depth and quality, complemented by a vibrant light blue that will catch the eye and add energy. Tan or gold accents could add an elegant touch and a feeling of warmth. We are aiming for a look that feels uplifting and engaging, with simplicity and elegance, yet stands out amid other brands on the shelf.

I am attaching the dimension of the bag.

Other information that needs to be listed:
Ingredients: 100% Arabica Coffee
Net Wt. 12 oz. (340 g)
Roasted and distributed by:
Name
Address
email

Text on the back of the bag:
Tollbury Coffee is crafted with a belief that kindness and positivity can spread, touching countless lives with every sip. This gourmet blend delivers a rich taste experience while giving back, as $2 from each bag sold is donated to local food banks to help those in need. Enjoy the warmth and goodness in each cup, knowing you’re making a difference with every purchase.

Thank you!

```html
<!DOCTYPE html>
<html lang="en">
<head>
<meta charset="utf-8">
<title>Tollbury Coffee – Bag Front</title>
<link rel="stylesheet" href="https://fonts.googleapis.com/css2?family=Marcellus&family=Montserrat:ital,wght@0,400;0,600;0,800;1,600&display=swap">
<style>
  :root{
    --backdrop:#d3dfe7;
    --navy:#0f1c3d;
    --navy-deep:#0a1126;
    --navy-pattern:#1a2f63;
    --gold:#d9b455;
    --gold-light:#f0d98a;
    --ink-light:#e9e4d2;
  }
  *{box-sizing:border-box;margin:0;padding:0}
  html,body{width:1200px;height:857px;overflow:hidden;background:var(--backdrop)}
  .canvas{position:relative;width:1200px;height:857px}
  .bag{position:absolute;left:355px;top:28px;width:490px;height:800px;background:var(--navy);overflow:hidden}
  .bag-pattern{position:absolute;inset:0;background:radial-gradient(ellipse at 20% 30%,var(--navy-pattern),transparent 60%),radial-gradient(ellipse at 85% 70%,var(--navy-pattern),transparent 60%),var(--navy)}
  .center-panel{position:absolute;left:140px;top:0;width:220px;height:100%;background:var(--navy-deep)}
  .gold-rule{position:absolute;top:0;width:2px;height:100%;background:var(--gold)}
  .gold-rule.left{left:140px}
  .gold-rule.right{left:358px}
  .brand{position:absolute;left:80px;top:200px;width:340px;height:170px;display:flex;flex-direction:column;align-items:center;justify-content:center;background:var(--navy-deep);border-radius:50%;gap:6px}
  .brand-dot{width:18px;height:18px;border-radius:50%;background:var(--gold)}
  .brand-name{font-family:"Marcellus",serif;color:var(--gold);font-size:36px;letter-spacing:1px;text-align:center;line-height:1.05}
  .label{position:absolute;left:60px;top:560px;width:390px;height:200px;background:var(--navy);border:3px solid var(--gold);outline:2px dashed var(--gold);outline-offset:3px;padding:12px 14px;color:var(--ink-light);font-family:"Montserrat",sans-serif}
  .label-brand{font-family:"Marcellus",serif;color:var(--gold);font-size:20px;text-align:center;width:170px}
  .label-arabica{font-size:11px;color:var(--ink-light);margin:4px 0 8px 40px;letter-spacing:.5px}
  .label-seal{position:absolute;right:16px;top:14px;width:54px;height:54px;border-radius:50%;border:1px solid var(--gold);opacity:.6}
  .label-grid{display:grid;grid-template-columns:1fr 1fr;gap:0 10px;border-top:1px solid var(--gold)}
  .tasting{font-size:6.5px;font-style:italic;text-align:center;padding:5px 2px;line-height:1.3}
  .origin{background:var(--gold);color:var(--navy-deep);padding:4px 6px}
  .origin-country{font-weight:800;font-size:15px;letter-spacing:.5px}
  .origin-farm{font-weight:800;font-size:8px;letter-spacing:.5px}
  .row{display:flex;align-items:center;gap:6px;padding:5px 0;border-top:1px solid var(--gold)}
  .tag{writing-mode:vertical-rl;transform:rotate(180deg);background:var(--gold);color:var(--navy-deep);font-size:5px;padding:2px 1px;font-weight:600}
  .roast-mark{width:18px;height:12px;border:1px solid var(--gold);border-radius:2px}
  .roast-mark.on{background:var(--gold)}
  .notes{font-size:8px;font-style:italic;font-weight:600}
  .meta{font-size:7.5px;line-height:1.35;padding-top:4px}
  .meta b{font-weight:600}
  .net{font-size:7px;font-weight:600;text-align:right}
</style>
</head>
<body>
<main class="canvas">
  <section class="bag">
    <div class="bag-pattern" role="img" aria-label="Tonal ornamental pattern in navy blue"></div>
    <div class="center-panel"></div>
    <div class="gold-rule left"></div>
    <div class="gold-rule right"></div>

    <div class="brand">
      <span class="brand-dot"></span>
      <span class="brand-name">TOLLBURY<br>COFFEE</span>
    </div>

    <div class="label">
      <div class="label-seal"></div>
      <div class="label-brand">TOLLBURY COFFEE</div>
      <div class="label-arabica">100% Arabica Coffee</div>
      <div class="label-grid">
        <div>
          <p class="tasting">"Fruity Aroma, Long Sweet Finish, Structured Acidity, Juicy And Silky Mouthfeel, Flavour Note of Apricot, Caramel, Mixed Berries And Chocolate"</p>
          <div class="row"><span class="tag">ROAST</span><span class="roast-mark on"></span><span class="roast-mark on"></span><span class="roast-mark"></span></div>
          <p class="meta"><b>Roasted</b> coffee<br><b>Whole</b> bean</p>
        </div>
        <div>
          <div class="origin">
            <div class="origin-country">COSTA RICA</div>
            <div class="origin-farm">HACIENDA SOLVERA</div>
          </div>
          <div class="row"><span class="tag">NOTES</span><span class="notes">Mixed Berries And Chocolate, Caramel</span></div>
          <div class="row">
            <p class="meta"><b>Traditional<br>Natural<br>Method</b></p>
            <p class="net">Net Wt.<br>12 oz. (340 g)</p>
          </div>
        </div>
      </div>
    </div>
  </section>
</main>
</body>
</html>
```